Window and GutterCleaning Flyer A5 size double sided.

We need a double sided A5 flyer. Side 1, is for window cleaning, side 2 is for gutter cleaning. Licensed by Borough of Marlow Council.
Phone number 0800 473 1926.
Business address 17 Fallowmere Close, North Brack Edinburgh EH31 4LP.
www.clearpane-hub-services.com
We use a LoftEye Gutter inspection Cam to view your gutters first to see if they need doing.
Window cleaning ; Professional window cleaning services, what we offer, water fed pole window cleaning able to reach windows up to 60 feet.
Conservatory cleaning.
Conservatory roof cleaning.
Fascias & Soffits cleaning.
Excellent Customer Service.
Target Market(s)
domestic houses
Industry/Entity Type
window cleaning
Look and feel
Each slider illustrates characteristics of the customer's brand and the style your logo design should communicate.

```html
<!DOCTYPE html>
<html lang="en">
<head>
<meta charset="utf-8">
<title>ClearPane Hub – Window &amp; Gutter Flyer</title>
<link href="https://fonts.googleapis.com/css2?family=Montserrat:wght@400;500;600;700;800;900&display=swap" rel="stylesheet">
<style>
:root{
  --stage:#8c8c8c;
  --navy:#252161;
  --navy-deep:#1d1950;
  --sky:#9cc7ef;
  --sky-bright:#7fb6ee;
  --sky-pale:#bcd9f5;
  --gold:#f6c21c;
  --red:#e1161f;
  --white:#ffffff;
  --ink:#1d1a3d;
}
*{margin:0;padding:0;box-sizing:border-box}
html,body{width:1200px;height:895px;overflow:hidden}
body{background:var(--stage);font-family:'Montserrat',sans-serif;position:relative;color:var(--ink)}
.page{position:absolute;top:97px;width:494px;height:701px;background:var(--white);overflow:hidden;box-shadow:0 6px 18px rgba(0,0,0,.35)}
.page--windows{left:81px}
.page--gutters{left:626px}
.abs{position:absolute}
.layer{position:absolute;left:0;top:0}

/* brand */
.brand{left:36px;top:42px;display:flex;align-items:center;gap:7px}
.brand__mark{width:16px;height:16px;background:var(--navy)}
.brand__name{font-weight:800;font-size:17px;color:var(--navy)}

/* side one headline */
.kicker{left:36px;top:128px;font-size:14px;font-weight:700;color:var(--ink)}
.headline{left:36px;top:146px;line-height:1}
.headline__light{display:block;font-weight:800;color:var(--sky-bright);font-size:34px}
.headline__dark{display:block;font-weight:900;color:var(--navy);font-size:35px;margin-top:2px}
.headline__sub{display:block;font-weight:800;color:var(--sky-bright);font-size:22px;margin-top:4px}
.intro{left:45px;top:249px;width:214px;font-size:8.3px;line-height:1.2;border-left:2px solid var(--navy);padding-left:6px;color:var(--ink)}

.reach-badge{left:355px;top:273px;width:104px;height:104px;border-radius:50%;background:var(--gold);border:3px dashed #f9d54d;color:var(--navy);text-align:center;display:flex;flex-direction:column;justify-content:center;font-size:6.8px;line-height:1.15;font-weight:500}
.reach-badge b{font-weight:800}
.reach-badge .reach-badge__big{font-size:15px;font-weight:800;margin-top:4px;color:var(--white);-webkit-text-stroke:0}

.photo-dot{width:84px;height:84px;border-radius:50%;border:3px solid var(--sky);background:radial-gradient(circle at 40% 35%,#dfe9f4,#6c8fb8 70%,#2d3a6b)}

.section-title{font-size:17px;font-weight:400;color:var(--white);letter-spacing:.5px}
.section-title b{font-weight:800;color:var(--sky-bright)}
.section-title--dark{color:var(--navy)}
.section-title--dark b{color:var(--navy)}

.offer-list{left:263px;top:389px;width:200px;list-style:none}
.offer-list li{display:flex;align-items:center;gap:8px;height:31px;border-bottom:1px dotted rgba(156,199,239,.6);color:var(--white);font-size:8.5px;font-weight:600}
.offer-list .icon{width:26px;height:26px;border-radius:50%;background:var(--sky);display:flex;align-items:center;justify-content:center;flex:none}

.licensed{display:flex;align-items:center;gap:10px}
.licensed__pill{background:var(--gold);color:var(--navy);font-weight:800;font-size:11px;border-radius:12px;padding:4px 11px}
.licensed__council{font-size:10px;font-weight:700;color:var(--white);line-height:1.1}

.ribbon{height:33px;background:var(--red);color:var(--white);font-size:9.6px;line-height:1.2;padding:5px 10px;clip-path:polygon(0 0,100% 0,94% 50%,100% 100%,0 100%)}
.ribbon b{font-weight:700}
.quote-cta{color:var(--white);font-size:9px;line-height:1}
.quote-cta b{display:block;font-size:14px;font-weight:800}

.contact{left:42px;top:610px;list-style:none;color:var(--white);font-size:9.6px}
.contact li{display:flex;align-items:flex-start;gap:6px;margin-bottom:5px;line-height:1.2}
.contact .dot{width:11px;height:11px;border-radius:50%;background:var(--sky);flex:none;margin-top:1px;display:flex;align-items:center;justify-content:center}

.testimonial{left:267px;top:587px;width:184px;height:114px;background:var(--sky);border-radius:18px 18px 0 0;text-align:center;font-size:10px;line-height:1.25;color:var(--navy);padding:26px 12px 0}
.quote-mark{left:335px;top:562px;font-size:64px;font-weight:900;color:var(--navy);line-height:1}

/* side two */
.g-kicker{left:38px;top:34px;font-size:13.5px;font-weight:800;color:var(--white)}
.g-headline{left:38px;top:50px;font-weight:800;font-size:24px;line-height:1.05}
.g-headline span{display:block}
.g-headline .light{color:var(--sky-bright)}
.g-headline .white{color:var(--white)}
.g-intro{left:38px;top:112px;border-left:2px solid var(--white);padding-left:6px;color:var(--white);font-size:9.4px;line-height:1.2;width:140px}

.cam-card{left:38px;top:212px;width:190px;height:110px;background:var(--sky);border-radius:12px}
.cam-card__photo{left:6px;top:8px;width:88px;height:96px;border-radius:8px;background:linear-gradient(160deg,#5d6a7b,#2c2f38 70%)}
.cam-card__text{left:107px;top:10px;width:80px;font-size:8px;line-height:1.25;color:var(--navy)}
.cam-card__text b{display:block;font-size:9.5px;font-weight:800}

.photo-dot--lg{width:92px;height:92px;border:2px solid var(--navy);background:radial-gradient(circle at 40% 35%,#e4ecf3,#8aa6bd 60%,#4e6b4c)}

.tick-list{left:37px;top:363px;list-style:none;font-size:8.4px;font-weight:600;color:var(--navy)}
.tick-list li{display:flex;align-items:center;gap:4px;height:14px}
.tick-list .tick{width:7px;height:7px;border-radius:50%;background:var(--sky-bright)}

.why-tab{left:145px;top:435px;width:206px;height:26px;background:var(--gold);border-radius:14px 14px 0 0;text-align:center;font-weight:800;font-size:11.5px;letter-spacing:3px;color:var(--navy);padding-top:6px}
.why-band{left:41px;top:459px;width:413px;height:90px;display:flex;border-radius:12px 12px 0 0;overflow:hidden}
.why-band__item{flex:1;background:var(--sky);display:flex;flex-direction:column;align-items:center;padding-top:14px;text-align:center;font-size:8.4px;line-height:1.2;color:var(--navy);font-weight:500}
.why-band__item:nth-child(2),.why-band__item:nth-child(4){background:var(--sky-pale)}
.why-band__item svg{margin-bottom:6px}

.g-quote{left:250px;top:573px;color:var(--white);font-size:17px;letter-spacing:3px;font-weight:400}
.g-quote b{color:var(--sky-bright);font-weight:800}
.values{left:248px;top:652px;font-size:9.5px;font-weight:800;color:var(--gold);letter-spacing:.3px}
.values .sep{color:var(--white);margin:0 4px}
.values .mid{color:var(--sky-bright)}
</style>
</head>
<body>

<!-- SIDE ONE : WINDOWS -->
<section class="page page--windows">
  <svg class="layer" width="494" height="701" viewBox="0 0 494 701">
    <defs>
      <linearGradient id="glassTone" x1="0" y1="0" x2="1" y2="1">
        <stop offset="0" stop-color="#bfe0fb"/>
        <stop offset=".55" stop-color="#5ea7e8"/>
        <stop offset="1" stop-color="#27508f"/>
      </linearGradient>
    </defs>
    <g role="img" aria-label="Photo of a cleaner abseiling down a tall glass building, framed in a house shape">
      <polygon points="290,194 384,110 494,190 494,320 290,320" fill="url(#glassTone)"/>
    </g>
    <polyline points="270,195 384,98 494,184" fill="none" stroke="var(--navy)" stroke-width="9" stroke-linejoin="miter"/>
    <rect x="447" y="125" width="13" height="36" fill="var(--navy)"/>
    <path d="M0 330 C30 312 60 322 100 316 C140 310 170 326 215 318 C250 312 275 322 300 316 C360 304 420 322 494 310 V701 H0 Z" fill="var(--navy)"/>
  </svg>

  <div class="abs brand"><span class="brand__mark"></span><span class="brand__name">ClearPane Hub</span></div>

  <p class="abs kicker">Let the Sunshine In</p>
  <h1 class="abs headline">
    <span class="headline__light">Sparkling</span>
    <span class="headline__dark">Window</span>
    <span class="headline__sub">Guaranteed</span>
  </h1>
  <p class="abs intro">We offer high-quality window cleaning for homes, giving every domestic property a spotless, streak-free result every time. Conservatory, roof, fascia and soffit cleaning too.</p>

  <div class="abs reach-badge">
    <span>WATER FED<br>POLE WINDOW<br>CLEANING ABLE</span>
    <b>TO REACH<br>WINDOWS UP TO</b>
    <span class="reach-badge__big">60 FEET</span>
  </div>

  <div class="abs photo-dot" role="img" aria-label="Photo of a squeegee wiping wet glass" style="left:37px;top:359px"></div>
  <div class="abs photo-dot" role="img" aria-label="Photo of a water fed pole brush on a window" style="left:135px;top:359px"></div>
  <div class="abs photo-dot" role="img" aria-label="Photo of two cleaners washing large windows" style="left:37px;top:454px"></div>
  <div class="abs photo-dot" role="img" aria-label="Photo of a rope access cleaner on a glass facade" style="left:135px;top:454px"></div>

  <h2 class="abs section-title" style="left:263px;top:355px">WE <b>OFFER</b></h2>
  <ul class="abs offer-list">
    <li><span class="icon"><svg width="14" height="14" viewBox="0 0 14 14"><path d="M1 7 L7 2 L13 7 V13 H1 Z M4 13 V8 M7 13 V8 M10 13 V8" fill="none" stroke="var(--navy)" stroke-width="1.2"/></svg></span>Conservatory Windows &amp; Roofs</li>
    <li><span class="icon"><svg width="14" height="14" viewBox="0 0 14 14"><path d="M1 6 L7 1 L13 6 M3 6 V13 H11 V6" fill="none" stroke="var(--navy)" stroke-width="1.2"/></svg></span>Fascia &amp; Soffit Cleaning</li>
    <li><span class="icon"><svg width="14" height="14" viewBox="0 0 14 14"><circle cx="7" cy="7" r="5.5" fill="none" stroke="var(--navy)" stroke-width="1.2"/><path d="M7 4 V7 L9.5 8.5" fill="none" stroke="var(--navy)" stroke-width="1.2"/></svg></span>One-off or Regular Cleans</li>
    <li><span class="icon"><svg width="14" height="14" viewBox="0 0 14 14"><path d="M3 7.5 L6 10.5 L11 4" fill="none" stroke="var(--navy)" stroke-width="1.6"/></svg></span>Reliable, Friendly Service</li>
  </ul>

  <div class="abs licensed" style="left:263px;top:529px">
    <span class="licensed__pill">LICENSED BY</span>
    <span class="licensed__council">Borough of Marlow Council</span>
  </div>

  <div class="abs ribbon" style="left:34px;top:560px;width:140px"><b>Based in North Brack</b><br>Serving All of Edinburgh</div>
  <p class="abs quote-cta" style="left:178px;top:562px">GET A<b>FREE<br>QUOTE</b></p>

  <ul class="abs contact">
    <li><span class="dot"></span>0800 473 1926</li>
    <li><span class="dot"></span>www.clearpane-hub-services.com</li>
    <li><span class="dot"></span>17 Fallowmere Close, North Brack,<br>Edinburgh EH31 4LP</li>
  </ul>

  <div class="abs testimonial">Great service from start to finish. Reliable, professional and the windows have never looked better!</div>
  <div class="abs quote-mark">“</div>
</section>

<!-- SIDE TWO : GUTTERS -->
<section class="page page--gutters">
  <svg class="layer" width="494" height="701" viewBox="0 0 494 701">
    <defs>
      <clipPath id="topBand">
        <path d="M0 0 H494 V178 C455 186 425 168 380 176 C330 186 300 170 250 180 C205 190 160 166 110 176 C70 184 40 170 0 186 Z"/>
      </clipPath>
      <linearGradient id="roofTone" x1="0" y1="0" x2="1" y2="1">
        <stop offset="0" stop-color="#f1f3f6"/>
        <stop offset=".6" stop-color="#c7ccd3"/>
        <stop offset="1" stop-color="#8c5a44"/>
      </linearGradient>
    </defs>
    <g clip-path="url(#topBand)">
      <rect width="494" height="200" fill="var(--navy)"/>
      <polygon points="340,0 494,0 494,200 262,200" fill="url(#roofTone)" role="img" aria-label="Photo of a white gutter, fascia and soffit under a brick roofline"/>
    </g>
    <path d="M0 542 C50 520 90 540 140 528 C200 514 240 536 300 524 C360 512 420 534 494 520 V701 H0 Z" fill="var(--navy)"/>
    <g fill="var(--sky)">
      <polygon points="304,18 385,18 385,10 405,33 385,56 385,48 304,48"/>
      <polygon points="274,70 355,70 355,62 375,85 355,108 355,100 274,100"/>
      <polygon points="245,128 324,128 324,120 344,143 324,166 324,158 245,158"/>
    </g>
    <g font-family="Montserrat, sans-serif" font-weight="800" font-size="12" fill="var(--navy)">
      <text x="320" y="38">GUTTER</text>
      <text x="297" y="90">FASCIA</text>
      <text x="268" y="148">SOFFIT</text>
    </g>
  </svg>

  <p class="abs g-kicker">Don’t Let Blocked</p>
  <h1 class="abs g-headline"><span class="light">Gutters Cause</span><span class="white">Costly Damage</span></h1>
  <p class="abs g-intro">We inspect before we clean — saving you time and money.</p>

  <div class="abs cam-card">
    <div class="abs cam-card__photo" role="img" aria-label="Photo of a gutter inspection camera screen on a pole"></div>
    <p class="abs cam-card__text"><b>Free Gutter Check</b>with LoftEye Inspection Cam. We show you what’s really going on before recommending service</p>
  </div>

  <div class="abs photo-dot photo-dot--lg" role="img" aria-label="Photo of a vacuum hose clearing a gutter" style="left:258px;top:215px"></div>
  <div class="abs photo-dot photo-dot--lg" role="img" aria-label="Photo of a gutter vacuum pole at a roofline" style="left:360px;top:215px"></div>
  <div class="abs photo-dot photo-dot--lg" role="img" aria-label="Photo of a mossy conservatory roof" style="left:258px;top:319px"></div>
  <div class="abs photo-dot photo-dot--lg" role="img" aria-label="Photo of a cleaner washing a roof with a pole" style="left:360px;top:319px"></div>

  <h2 class="abs section-title section-title--dark" style="left:37px;top:336px">WE <b>OFFER</b></h2>
  <ul class="abs tick-list">
    <li><span class="tick"></span>Safe, No-Ladder Cleaning</li>
    <li><span class="tick"></span>Removes Moss, Leaves &amp; Debris</li>
    <li><span class="tick"></span>Prevents Overflow, Damp &amp; Water Damage</li>
    <li><span class="tick"></span>Fast, Clean &amp; Fully Insured</li>
  </ul>

  <div class="abs why-tab">WHY CHOOSE US?</div>
  <div class="abs why-band">
    <div class="why-band__item"><svg width="22" height="18" viewBox="0 0 22 18"><circle cx="6" cy="4" r="3" fill="var(--navy)"/><circle cx="16" cy="4" r="3" fill="var(--navy)"/><path d="M1 18 V11 Q6 6 11 11 Q16 6 21 11 V18 Z" fill="var(--navy)"/></svg>Friendly,<br>professional<br>service</div>
    <div class="why-band__item"><svg width="20" height="20" viewBox="0 0 20 20"><circle cx="10" cy="10" r="7" fill="none" stroke="var(--navy)" stroke-width="3" stroke-dasharray="3 2"/><path d="M7 10 L9.5 12.5 L13.5 7.5" fill="none" stroke="var(--navy)" stroke-width="1.6"/></svg>Reliable and<br>efficient</div>
    <div class="why-band__item"><svg width="18" height="20" viewBox="0 0 18 20"><rect x="2" y="1" width="12" height="16" rx="1" fill="var(--navy)"/><path d="M5 5 H11 M5 8 H11 M5 11 H9" stroke="var(--sky)" stroke-width="1.2"/><circle cx="14" cy="15" r="3.5" fill="var(--navy)" stroke="var(--sky-pale)"/></svg>Fully licensed<br>and insured</div>
    <div class="why-band__item"><svg width="24" height="20" viewBox="0 0 24 20"><circle cx="6" cy="9" r="2.5" fill="var(--navy)"/><circle cx="12" cy="8" r="3" fill="var(--navy)"/><circle cx="18" cy="9" r="2.5" fill="var(--navy)"/><path d="M2 19 Q6 12 10 16 Q12 11 14 16 Q18 12 22 19 Z" fill="var(--navy)"/><path d="M7 3 L8 1 L9 3 M11 2 L12 0 L13 2 M15 3 L16 1 L17 3" stroke="var(--navy)" fill="none"/></svg>Excellent<br>customer<br>satisfaction</div>
  </div>

  <div class="abs ribbon" style="left:33px;top:567px;width:188px"><b>Stay Ahead of Leaks</b><br>Book Your Gutter Check Today!</div>

  <ul class="abs contact">
    <li><span class="dot"></span>0800 473 1926</li>
    <li><span class="dot"></span>www.clearpane-hub-services.com</li>
    <li><span class="dot"></span>17 Fallowmere Close, North Brack,<br>Edinburgh EH31 4LP</li>
  </ul>

  <p class="abs g-quote">GET A <b>FREE QUOTE</b></p>
  <div class="abs licensed" style="left:248px;top:609px;padding-bottom:8px;border-bottom:1px solid rgba(255,255,255,.35);width:210px">
    <span class="licensed__pill">LICENSED BY</span>
    <span class="licensed__council">Borough of Marlow Council</span>
  </div>
  <p class="abs values">PROFESSIONAL<span class="sep">|</span><span class="mid">AFFORDABLE</span><span class="sep">|</span>LOCAL</p>
</section>

</body>
</html>
```